Brookmere Osteopathy flyer

I want a clean clear DL flyer (but also want an A4 poster) promoting a new Osteopathic business in a semi rural area in Tasmania (Australia).
It can have pictures like the examples attached to show people what Osteopathy is (its like Chiropractic and physiotherapy).
I am the sole practioner and am male, so any pictures would be best to be a white male if possible.
I've attached some wording, you can use all, or none of it
I don't have a phone number for the business yet
info@brookmereosteopathy.example
www.brookmereosteopathy.example
Target Market(s)
Australians, from tradies, professionals, babies to retired people
Industry/Entity Type
Health
Look and feel

```html
<!DOCTYPE html>
<html lang="en">
<head>
<meta charset="utf-8">
<title>Brookmere Osteopathy – DL Flyer</title>
<link href="https://fonts.googleapis.com/css2?family=Oswald:wght@400&family=Saira+Condensed:wght@600;700&family=Nunito:wght@400;600;700&display=swap" rel="stylesheet">
<style>
  :root {
    --blue: #168bd0;
    --orange: #f3952f;
    --ink: #1f1f1f;
    --paper: #ffffff;
    --stage: #ececec;
  }
  * { box-sizing: border-box; margin: 0; padding: 0; }
  html, body { width: 1191px; height: 1200px; overflow: hidden; }
  body { background: var(--stage); position: relative; font-family: "Nunito", sans-serif; color: var(--ink); }

  .flyer { position: absolute; top: 87px; width: 482px; height: 1026px; background: var(--paper); overflow: hidden; }
  .flyer--front { left: 99px; }
  .flyer--back { left: 611px; }
  .abs { position: absolute; }

  .accent-block { position: absolute; top: 0; width: 121px; height: 99px; }
  .accent-block--blue { right: 0; background: var(--blue); }
  .accent-block--orange { left: 1px; background: var(--orange); }

  .photo { position: absolute; }

  .brand-mark { position: absolute; width: 136px; height: 136px; border: 2px solid var(--blue); border-radius: 50%;
    display: flex; align-items: center; justify-content: center; text-align: center; }
  .brand-mark span { font-family: "Oswald", sans-serif; font-weight: 400; font-size: 17px; line-height: 1.2; color: var(--blue); text-transform: uppercase; letter-spacing: .5px; }

  .services-title { left: 17px; top: 182px; width: 188px; font-family: "Oswald", sans-serif; font-weight: 400; font-size: 28px; line-height: 35px; color: var(--ink); text-transform: uppercase; white-space: nowrap; }

  .offer { left: 244px; top: 340px; width: 175px; font-family: "Saira Condensed", sans-serif; font-weight: 700; color: var(--blue); text-align: center; text-transform: uppercase; }
  .offer__top { font-size: 37px; line-height: 40px; }
  .offer__main { font-size: 64px; line-height: 58px; }
  .offer__bottom { font-size: 32px; line-height: 36px; }

  .intro { left: 15px; top: 508px; width: 228px; font-size: 12.3px; line-height: 25.5px; white-space: nowrap; }
  .intro p + p { margin-top: 9px; line-height: 28.8px; }

  .tagline { left: 9px; top: 880px; width: 466px; font-family: "Saira Condensed", sans-serif; font-weight: 600; font-size: 26.5px; line-height: 34px; color: var(--blue); white-space: nowrap; }
  .tagline em { font-style: normal; color: var(--orange); }

  .footer { position: absolute; left: 0; bottom: 0; width: 100%; height: 91px; background: var(--blue); color: #fff; }
  .contact-list { position: absolute; left: 17px; top: 24px; list-style: none; font-size: 11px; font-weight: 600; line-height: 19.6px; }
  .contact-list li { display: flex; align-items: center; gap: 7px; }
  .contact-list svg { width: 11px; height: 11px; flex: none; }
  .phone { position: absolute; display: flex; align-items: center; gap: 12px; font-family: "Saira Condensed", sans-serif; font-weight: 600; font-size: 33px; color: #fff; }
  .phone svg { width: 32px; height: 34px; }
  .flyer--front .phone { left: 261px; top: 26px; }
  .flyer--back .phone { left: 258px; top: 23px; }

  .region { left: 294px; top: 217px; width: 180px; font-family: "Oswald", sans-serif; font-weight: 400; font-size: 22.5px; line-height: 33px; text-transform: uppercase; color: var(--ink); }

  .reasons-title { left: 20px; top: 347px; width: 455px; font-family: "Saira Condensed", sans-serif; font-weight: 700; font-size: 51px; line-height: 52px; color: var(--blue); }
  .reasons { left: 20px; top: 464px; list-style: none; }
  .reasons li { display: flex; align-items: center; height: 46px; font-size: 20.5px; font-weight: 600; color: var(--ink); }
  .reasons svg { width: 21px; height: 14px; margin-right: 12px; flex: none; }

  .slogan { position: absolute; left: 20px; top: 10px; font-family: "Saira Condensed", sans-serif; font-weight: 600; font-size: 35px; line-height: 37px; color: #fff; }
</style>
</head>
<body>

<!-- Front side -->
<section class="flyer flyer--front">
  <div class="accent-block accent-block--blue"></div>
  <div class="brand-mark" style="left:19px; top:22px;"><span>Brookmere<br>Osteopathy</span></div>

  <div class="photo" role="img" aria-label="Practitioner assessing a smiling patient's shoulder in a bright clinic"
       style="left:211px; top:19px; width:247px; height:298px; background:linear-gradient(160deg,#eef0f0 0%,#d9dcdc 45%,#e9a43a 70%,#3d5f8f 100%);"></div>

  <h1 class="abs services-title">Chiropractic<br>and<br>Physiotherapy</h1>

  <div class="photo" role="img" aria-label="Woman lying on a treatment table receiving neck and head therapy"
       style="left:1px; top:335px; width:211px; height:161px; background:linear-gradient(120deg,#c9ccd8 0%,#e4e5ec 45%,#b89a85 70%,#2a2f3a 100%);"></div>

  <div class="abs offer">
    <div class="offer__top">Free Intial</div>
    <div class="offer__main">Physio</div>
    <div class="offer__bottom">Consultation</div>
  </div>

  <div class="abs intro">
    <p>Brookmere Osteopathy use a tailored<br>combination of joint mobilisation/<br>manipulation, stretching, movement,<br>trigger point dry needling and<br>targeted massage to reduce pain and<br>restore optimal function.</p>
    <p>Hands-on treatment is backed up<br>with rehabilitative exercise prescrip-<br>tion and advice. So whether you're<br>recovering from injury or managing<br>chronic discomfort, we’re here to help<br>you move better and feel your best.</p>
  </div>

  <div class="photo" role="img" aria-label="Sleeping baby in blue receiving gentle cranial treatment"
       style="left:245px; top:520px; width:221px; height:157px; background:linear-gradient(170deg,#b9b6cc 0%,#d8d0d4 40%,#3f88b8 75%,#8fa6c0 100%);"></div>
  <div class="photo" role="img" aria-label="Practitioner pointing to a model of the human spine"
       style="left:246px; top:685px; width:221px; height:173px; background:linear-gradient(110deg,#eef3f8 0%,#f7f3ea 45%,#e8d9a6 60%,#f2f5f8 100%);"></div>

  <p class="abs tagline">Serving Semi Rural <em>Area In Tasmania - Australia</em></p>

  <footer class="footer">
    <ul class="contact-list">
      <li><svg viewBox="0 0 12 12"><path d="M6 0.5a4 4 0 0 0-4 4c0 3 4 7 4 7s4-4 4-7a4 4 0 0 0-4-4z" fill="var(--orange)"/><circle cx="6" cy="4.5" r="1.5" fill="var(--blue)"/></svg>48 Ridgeline Road, Brookmere</li>
      <li><svg viewBox="0 0 12 12"><rect x="1" y="3" width="10" height="7" rx="1" fill="none" stroke="var(--orange)" stroke-width="1.4"/><path d="M1.5 3.5L6 7l4.5-3.5" fill="none" stroke="var(--orange)" stroke-width="1.4"/></svg>info@brookmereosteopathy.example</li>
      <li><svg viewBox="0 0 12 12"><circle cx="6" cy="6" r="5" fill="none" stroke="var(--orange)" stroke-width="1.2"/><ellipse cx="6" cy="6" rx="2.2" ry="5" fill="none" stroke="var(--orange)" stroke-width="1"/><path d="M1 6h10" stroke="var(--orange)" stroke-width="1"/></svg>www.brookmereosteopathy.example</li>
    </ul>
    <div class="phone">
      <svg viewBox="0 0 32 34"><path d="M8 4l5 7-3 3c1.5 4 5 8 9 10l3-3 7 5-3 5C15 31 3 19 3 8z" fill="none" stroke="var(--orange)" stroke-width="2" stroke-linejoin="round"/><path d="M19 4a9 9 0 0 1 9 9M19 9a4 4 0 0 1 4 4" fill="none" stroke="var(--orange)" stroke-width="2" stroke-linecap="round"/></svg>
      000.111.2222
    </div>
  </footer>
</section>

<!-- Back side -->
<section class="flyer flyer--back">
  <div class="accent-block accent-block--orange"></div>
  <div class="photo" role="img" aria-label="Osteopath performing a spinal manipulation on a patient lying on a treatment table"
       style="left:25px; top:19px; width:247px; height:298px; background:linear-gradient(170deg,#dcdcd8 0%,#c9c7c2 40%,#2f3f5c 60%,#b59b7c 85%,#d9d6d0 100%);"></div>
  <div class="brand-mark" style="left:297px; top:56px;"><span>Brookmere<br>Osteopathy</span></div>

  <p class="abs region">Serving semi rural area in Tasmania, Australia</p>

  <h2 class="abs reasons-title">Common Reasons People Visit An Osteopath</h2>

  <ul class="abs reasons">
    <li><svg viewBox="0 0 21 14"><path d="M1 13c3-6 8-8 15-8" fill="none" stroke="var(--orange)" stroke-width="3"/><path d="M13 1l7 4-7 5z" fill="var(--orange)"/></svg>Back / Neck Pain</li>
    <li><svg viewBox="0 0 21 14"><path d="M1 13c3-6 8-8 15-8" fill="none" stroke="var(--orange)" stroke-width="3"/><path d="M13 1l7 4-7 5z" fill="var(--orange)"/></svg>Headaches / Migraines</li>
    <li><svg viewBox="0 0 21 14"><path d="M1 13c3-6 8-8 15-8" fill="none" stroke="var(--orange)" stroke-width="3"/><path d="M13 1l7 4-7 5z" fill="var(--orange)"/></svg>Joint And Muscle Pain</li>
    <li><svg viewBox="0 0 21 14"><path d="M1 13c3-6 8-8 15-8" fill="none" stroke="var(--orange)" stroke-width="3"/><path d="M13 1l7 4-7 5z" fill="var(--orange)"/></svg>Pregnancy-related Discomfort</li>
    <li><svg viewBox="0 0 21 14"><path d="M1 13c3-6 8-8 15-8" fill="none" stroke="var(--orange)" stroke-width="3"/><path d="M13 1l7 4-7 5z" fill="var(--orange)"/></svg>Disc Related Issues</li>
    <li><svg viewBox="0 0 21 14"><path d="M1 13c3-6 8-8 15-8" fill="none" stroke="var(--orange)" stroke-width="3"/><path d="M13 1l7 4-7 5z" fill="var(--orange)"/></svg>Sciatica</li>
    <li><svg viewBox="0 0 21 14"><path d="M1 13c3-6 8-8 15-8" fill="none" stroke="var(--orange)" stroke-width="3"/><path d="M13 1l7 4-7 5z" fill="var(--orange)"/></svg>Plantar Fasciitis</li>
    <li><svg viewBox="0 0 21 14"><path d="M1 13c3-6 8-8 15-8" fill="none" stroke="var(--orange)" stroke-width="3"/><path d="M13 1l7 4-7 5z" fill="var(--orange)"/></svg>Tendonitis / Bursitis</li>
    <li><svg viewBox="0 0 21 14"><path d="M1 13c3-6 8-8 15-8" fill="none" stroke="var(--orange)" stroke-width="3"/><path d="M13 1l7 4-7 5z" fill="var(--orange)"/></svg>Adhesive Capsulitis (Frozen Shoulder)</li>
    <li><svg viewBox="0 0 21 14"><path d="M1 13c3-6 8-8 15-8" fill="none" stroke="var(--orange)" stroke-width="3"/><path d="M13 1l7 4-7 5z" fill="var(--orange)"/></svg>Tennis / Golfers Elbow</li>
  </ul>

  <footer class="footer">
    <p class="slogan">Move Better,<br>Feel Better.</p>
    <div class="phone">
      <svg viewBox="0 0 32 34"><path d="M8 4l5 7-3 3c1.5 4 5 8 9 10l3-3 7 5-3 5C15 31 3 19 3 8z" fill="none" stroke="var(--orange)" stroke-width="2" stroke-linejoin="round"/><path d="M19 4a9 9 0 0 1 9 9M19 9a4 4 0 0 1 4 4" fill="none" stroke="var(--orange)" stroke-width="2" stroke-linecap="round"/></svg>
      000.111.2222
    </div>
  </footer>
</section>

</body>
</html>
```